Tiny Meadow Product Label for Tear-Free Head-to-Toe Wash

Need a bottle label design for a new line of natural products targeting infants and children. Products are Pediatrician-developed and paraben-free, sulfate-free, fragrance-free, and cruelty-free. Design should be clean and have a high-end feel to it. Will need other product labels in Tiny Meadow line designed as well in upcoming projects.

Target Market(s)

Newborn to young elementary age children and their parents

Industry/Entity Type

Cosmetics/Beauty

Font styles to use
Other font styles liked:
• Brand fonts are Jost and Sonorous

Colors

Designer to choose colors to be used in the design.

Requirements
Must have
• Tiny Meadow logo, Pediatrician Developed logo, and a clean high-end feel to it. The label must fit the specialty bottle we will be using (label measurements and diagram will be provided) for the front and back of bottle only (NOT the side labels). It must include our list of ingredients (will provide once designer selected).
Nice to have
• Should stand out on the shelf of other baby products due to it's clean simplicity and high-end feel
Should not have
• too much of a "kiddie" feel to it (targeting the parents not the kids)

```html
<!DOCTYPE html>
<html lang="en">
<head>
<meta charset="UTF-8">
<title>Tiny Meadow – Tear-Free Head-to-Toe Wash Labels</title>
<link href="https://fonts.googleapis.com/css2?family=Jost:ital,wght@0,400;0,500;0,600;0,700;1,600;1,700&family=Roboto+Condensed:wght@400&display=swap" rel="stylesheet">
<style>
  :root {
    --canvas: #ffffff;
    --label: #fbf8f4;
    --ink: #141414;
    --body-ink: #2a2a2a;
    --gold: #9a7330;
    --gold-soft: #b8915a;
    --face-fill: #f3efe7;
  }
  * { margin: 0; padding: 0; box-sizing: border-box; }
  html, body {
    width: 1200px; height: 1200px; overflow: hidden;
    background: var(--canvas);
    font-family: "Jost", sans-serif;
    color: var(--ink);
  }
  .sheet { position: relative; width: 1200px; height: 1200px; }

  .label {
    position: absolute;
    top: 270px;
    width: 440px;
    height: 660px;
    background: var(--label);
    border-radius: 50% 50% 0 0 / 11% 11% 0 0;
    box-shadow: 0 0 0 1px #eeeae3;
  }
  .label--front { left: 140px; }
  .label--back  { left: 620px; }

  /* Front */
  .brand-name {
    position: absolute;
    left: 18px;
    bottom: 60px;
    transform-origin: left bottom;
    transform: rotate(-90deg) translateY(100%);
    font-weight: 700;
    font-size: 66px;
    letter-spacing: 1px;
    line-height: 1;
    white-space: nowrap;
    color: var(--ink);
  }
  .hero-art {
    position: absolute;
    left: 235px; top: 120px;
    width: 150px; height: 150px;
    border-radius: 50%;
    background: var(--face-fill);
    border: 3px solid var(--gold);
  }
  .product-title {
    position: absolute;
    right: 40px; top: 335px;
    width: 260px;
    text-align: right;
    font-weight: 600;
    font-size: 30px;
    line-height: 1.15;
    color: var(--ink);
  }
  .tagline {
    position: absolute;
    left: 155px; right: 0; top: 413px;
    height: 30px;
    background: var(--gold);
    border-radius: 15px 0 0 15px;
    color: #fff;
    font-family: "Roboto Condensed", sans-serif;
    font-size: 14.5px;
    line-height: 30px;
    padding-left: 20px;
  }
  .claims {
    position: absolute;
    left: 160px; top: 460px;
    display: flex; gap: 14px;
  }
  .claim-badge {
    width: 50px; height: 50px;
    border-radius: 50%;
    border: 1.5px dashed var(--body-ink);
  }
  .net-wt {
    position: absolute;
    right: 40px; top: 585px;
    font-weight: 600;
    font-size: 17px;
    color: var(--gold);
  }

  /* Back */
  .back-icon {
    position: absolute;
    left: 50%; top: 30px;
    width: 54px; height: 54px;
    margin-left: -27px;
    border-radius: 50%;
    background: var(--face-fill);
    border: 2px solid var(--gold);
  }
  .back-copy {
    position: absolute;
    left: 58px; right: 58px; top: 100px;
    font-size: 14.5px;
    line-height: 1.5;
    color: var(--body-ink);
  }
  .back-copy p { text-align: justify; text-align-last: center; }
  .back-copy h2 {
    font-style: italic;
    font-weight: 700;
    font-size: 19px;
    color: var(--gold);
    text-align: center;
    margin: 12px 0 4px;
  }
  .maker {
    position: absolute;
    left: 58px; top: 560px;
    font-size: 14.5px;
    line-height: 1.45;
    color: var(--body-ink);
  }
  .maker strong { color: var(--gold); font-style: italic; font-weight: 700; }
  .ped-badge {
    position: absolute;
    right: 56px; top: 550px;
    width: 66px; height: 66px;
    border-radius: 50%;
    border: 1.5px solid var(--gold);
  }
</style>
</head>
<body>
<main class="sheet">

  <section class="label label--front">
    <div class="brand-name">Tiny Meadow</div>
    <div class="hero-art" role="img" aria-label="Illustration of a sleeping baby with sun rays"></div>
    <h1 class="product-title">Tear-Free Head-to-Toe Wash</h1>
    <div class="tagline">Naturally formulated for delicate skin</div>
    <div class="claims">
      <div class="claim-badge" role="img" aria-label="Paraben free badge"></div>
      <div class="claim-badge" role="img" aria-label="Sulfate free badge"></div>
      <div class="claim-badge" role="img" aria-label="Fragrance free badge"></div>
      <div class="claim-badge" role="img" aria-label="Cruelty free badge"></div>
    </div>
    <div class="net-wt">Net wt: 73 mL/2,43 fl.oz</div>
  </section>

  <section class="label label--back">
    <div class="back-icon" role="img" aria-label="Small sleeping baby illustration"></div>
    <div class="back-copy">
      <p>A gentle, all-in-one cleanser made with natural ingredients to protect and nourish baby’s delicate hair and skin. Pediatrician-developed and suitable for daily use from newborn onwards.</p>
      <h2>Directions:</h2>
      <p>Dispense a small amount into hands or washcloth. Gently massage into wet hair and skin. Rinse thoroughly. Avoid contact with eyes.</p>
      <h2>Ingredients:</h2>
      <p>Aqua, Glycerin, Decyl Glucoside, Sodium Lauroyl Lactylate, Coco-Glucoside, Glyceryl Oleate, Xanthan Gum, Sodium Benzoate, Citric Acid. (Full list to be finalized.)</p>
    </div>
    <div class="maker">
      <strong>Manufactured for</strong><br>
      Tiny Meadow Co.<br>
      tinymeadowcare.com/Made in USA
    </div>
    <div class="ped-badge" role="img" aria-label="Pediatrician developed badge"></div>
  </section>

</main>
</body>
</html>
```